Coastline Premier Retreats Business Card Design

Design a business card for Coastline Premier Retreats. Look at the website for colors and reference. Card should have logo, name, title, office number, mobile number, email, URL and a tagline like, "Luxury Hotel & Resort Email Marketing" (This might change).

https://www.coastlinepremierretreats.example

The rest I will leave up to your imagination.

Contact Information for Business Card

Logo, name, title, office number, mobile number, email, URL and a tagline like, "Luxury Hotel & Resort Email Marketing" (This might change).

```html
<!DOCTYPE html>
<html lang="en">
<head>
<meta charset="utf-8">
<title>Coastline Premier Retreats – Business Card</title>
<link rel="stylesheet" href="https://fonts.googleapis.com/css2?family=Montserrat:wght@400;500;700;800&display=swap">
<style>
  :root {
    --bg: #2a2a2a;
    --card: #171717;
    --orange: #ef7412;
    --white: #ffffff;
    --soft: #d9d9d9;
    --logo-grey: #5a5a5a;
  }
  * { margin: 0; padding: 0; box-sizing: border-box; }
  html, body {
    width: 1200px; height: 900px; overflow: hidden;
    background: var(--bg);
    font-family: "Montserrat", sans-serif;
  }
  .stage { position: relative; width: 1200px; height: 900px; }
  .card {
    position: absolute; left: 250px; width: 700px; height: 400px;
    background: var(--card);
    box-shadow: 0 14px 34px rgba(0,0,0,.45);
    overflow: hidden;
  }
  .card--front { top: 36px; }
  .card--back { top: 466px; }

  /* front */
  .name-band {
    position: absolute; left: 24px; top: 34px; width: 400px; height: 48px;
    background: var(--orange);
    display: flex; align-items: center; padding-left: 56px;
  }
  .name-band__text {
    font-weight: 800; font-size: 27px; letter-spacing: 1px;
    color: var(--card); text-transform: uppercase;
  }
  .brand-mark {
    position: absolute; left: 442px; top: 36px;
    display: flex; align-items: center; gap: 10px;
  }
  .brand-mark__square { width: 12px; height: 12px; background: var(--orange); flex: none; }
  .brand-mark__name {
    font-weight: 700; font-size: 17px; line-height: 1.15;
    color: var(--white); text-transform: uppercase; letter-spacing: .5px;
  }
  .job-title {
    position: absolute; left: 80px; top: 92px;
    font-size: 15px; color: var(--soft);
  }
  .address {
    position: absolute; left: 80px; top: 148px;
    font-size: 15px; line-height: 1.45; color: var(--white);
    font-style: normal;
  }
  .contact-list {
    position: absolute; left: 58px; top: 212px; list-style: none;
    font-size: 15px; line-height: 26px; color: var(--white);
  }
  .contact-list li { display: flex; align-items: center; gap: 10px; }
  .contact-list svg { width: 13px; height: 13px; flex: none; fill: var(--orange); }

  /* back */
  .back-brand {
    position: absolute; left: 0; right: 0; top: 120px; text-align: center;
    font-weight: 800; font-size: 40px; letter-spacing: 2px; line-height: 1.1;
    color: var(--logo-grey); text-transform: uppercase;
  }
  .tagline {
    position: absolute; left: 0; right: 0; top: 282px; text-align: center;
    font-size: 19px; font-weight: 500; color: var(--orange);
  }
</style>
</head>
<body>
<main class="stage">

  <section class="card card--front" aria-label="Business card front">
    <div class="name-band"><span class="name-band__text">Daniel Mercer</span></div>
    <div class="brand-mark">
      <span class="brand-mark__square"></span>
      <span class="brand-mark__name">Coastline Premier<br>Retreats</span>
    </div>
    <p class="job-title">CEO/Founder</p>
    <address class="address">PO Box 456, 88 Harbor Rd<br>Seaview, CA 90210</address>
    <ul class="contact-list">
      <li>
        <svg viewBox="0 0 16 16" aria-hidden="true"><path d="M4 0h8a1 1 0 0 1 1 1v14a1 1 0 0 1-1 1H4a1 1 0 0 1-1-1V1a1 1 0 0 1 1-1zm1 2v10h6V2zm3 11a1 1 0 1 0 0 2 1 1 0 0 0 0-2z"/></svg>
        555.214.0187
      </li>
      <li>
        <svg viewBox="0 0 16 16" aria-hidden="true"><path d="M3.6 1 6 3.8 4.7 5.6c.9 2 2.7 3.8 4.7 4.7L11.2 9 14 11.4l-1.2 2.8C6.6 14 2 9.4 1.8 3.2z"/></svg>
        +1 555 302 4419
      </li>
      <li>
        <svg viewBox="0 0 16 16" aria-hidden="true"><path d="M1 3h14v10H1zm1.5 1.2v.4L8 8.6l5.5-4v-.4zM2.5 6.3v5.5h11V6.3L8 10.2z"/></svg>
        info@coastlinepremierretreats.example
      </li>
      <li>
        <svg viewBox="0 0 16 16" aria-hidden="true"><path d="M8 1a7 7 0 1 0 0 14A7 7 0 0 0 8 1zm0 1.5c.9 0 1.9 1.8 2.2 4.5H5.8C6.1 4.3 7.1 2.5 8 2.5zM2.6 7H4.3c.1-1.5.4-2.8.9-3.8A5.5 5.5 0 0 0 2.6 7zm9.1 0h1.7a5.5 5.5 0 0 0-2.6-3.8c.5 1 .8 2.3.9 3.8zM2.6 9a5.5 5.5 0 0 0 2.6 3.8c-.5-1-.8-2.3-.9-3.8zm3.2 0c.3 2.7 1.3 4.5 2.2 4.5s1.9-1.8 2.2-4.5zm5.9 0c-.1 1.5-.4 2.8-.9 3.8A5.5 5.5 0 0 0 13.4 9z"/></svg>
        www.coastlinepremierretreats.example
      </li>
    </ul>
  </section>

  <section class="card card--back" aria-label="Business card back">
    <p class="back-brand">Coastline Premier<br>Retreats</p>
    <p class="tagline">Luxury Hotel &amp; Resort Email Marketing</p>
  </section>

</main>
</body>
</html>
```